Local Chiropractoc needs Modern Website

This website needs to have an upscale look with a very modern feel.

This is for a home page psd layout and an interior page psd file so 2 files total

Below is the information and websites to reference

Add Logo that is attached.

Build a color scheme similar to this website image titled "chiro-1" using the golds, whites, blacks and browns from the color of the logo

I want to see a light background so it makes the images and logo stick out

Must Include these pages in a horizontal menu bar in this order:
Home, Why Fair Ridge?, How Chiropractic Helps, Ask the Doctor, Work Place Wellness, Request an Appointment, Blog, Contact Us

Please add the following social media logos to the top and footer of the website: Chatterly, Plexo+, Vidzio

Build a "classy looking" Make An Appointment Button into the header with the contact info below

Phone Number:
555-014-2297

Address:
4172 North Maple Blvd, Suite #7
Brookhaven, FL 34720

This website needs 4 rotating banners. Please reference a layout similar to this for the banners: http://hollowpinespine.com/. However design it nicer than this website

Below are the description for each banner

Rotating Banner #1
Use Image: Patients are Saying
Add a line of text: "What our Patients are Saying"

Rotating Banner #2
Use Image: Becoming a Patient
Add a line of text: "Interested in Becoming a Patient"

Rotating Banner #3
Use Image: Dinner with Doctor
Add a line of text: "Win A free Dinner with Dr. Hollins"

Rotating Banner #4
Use Image: Chatterly
Add a line of text: Follow us on Chatterly
Bullet point these 4 lines underneath the "Follow us on Chatterly" text:
- Cutting Edge Health News
- Healthy Recipes
- Newest Health Products
- Clinic Events

I'd like to see a free consultation box similar to the "chiro-1" image. Fields to include are: First Name, Last Name, Phone Number, Comments

For the body, please fill it with latin text. Please design a professional 2 column layout similar to the www.hollowpinespine.com website. (DO NOT COPY THIS WEBSITE, USE IT AS REFERENCE)

In the left column include in this order:
Video
Rate us on Plexo Button, Find us on Chatterly Button
Welcome Letter

In the right column include this:

Office Hours
Monday: 8:00-11:00, 2:00-5:00
Tuesday: 8:30-11:00, 2:00-5:30
Wednesday: 8:00-11:00, 2:00-5:00
Thursday: 10:00-12:00, 2:30-5:00
Friday: 8:00-10:00, 1:00-5:00
Saturday: Closed
Sunday: Closed

Patient Testimonials
Fill with a latin text testimonial. This spot will rotate different testimonials

For the footer please design something similar to the layout of this: http://www.tidewellhealer.com/

Also include in the Footer: Powered by Crestline Pixel Group

```html
<!DOCTYPE html>
<html lang="en">
<head>
<meta charset="utf-8">
<title>Fair Ridge Chiropractic</title>
<link href="https://fonts.googleapis.com/css2?family=Open+Sans:ital,wght@0,400;0,600;0,700;1,400&family=Ubuntu:wght@500;700&display=swap" rel="stylesheet">
<style>
:root{
  --gold:#b89a5a;
  --gold-dark:#a48748;
  --ink:#2c2c2c;
  --ink-soft:#3a3a3a;
  --paper:#f2eee7;
  --white:#ffffff;
  --line:#e6e6e6;
  --row:#f3f3f3;
  --text:#666666;
}
*{box-sizing:border-box;margin:0;padding:0}
html,body{width:912px;height:1200px;overflow:hidden}
body{background:var(--paper);font-family:"Open Sans",sans-serif;color:var(--text);position:relative}
.abs{position:absolute}

/* header */
.brand{left:122px;top:50px;width:180px;font-family:"Ubuntu",sans-serif;font-weight:700;color:var(--ink);line-height:1}
.brand .name{font-size:30px;letter-spacing:-.5px;display:block;white-space:nowrap}
.brand .sub{font-size:16px;letter-spacing:1px;display:block;margin-top:5px}
.social-top{left:740px;top:56px;display:flex;gap:5px}
.social-dot{width:20px;height:20px;border-radius:50%;border:1px solid var(--gold);color:var(--gold);font-size:8px;font-weight:700;display:flex;align-items:center;justify-content:center}
.social-dot.on{background:var(--gold);color:var(--white)}
.contact-bar{left:393px;top:88px;width:413px;height:35px;display:flex}
.contact-bar .info{background:var(--ink);display:flex;align-items:center;color:var(--white);height:100%}
.contact-bar .item{display:flex;align-items:center;gap:8px;padding:0 10px;height:100%;white-space:nowrap}
.contact-bar .item+.item{border-left:1px solid #444}
.contact-bar b{display:block;font-size:8px}
.contact-bar i{display:block;font-size:7.5px;color:#999}
.appt{flex:1;position:relative;display:flex;align-items:center;justify-content:center;color:var(--white);font-size:8px;font-weight:700;letter-spacing:.3px;white-space:nowrap}
.appt svg{position:absolute;left:0;top:0}
.appt span{position:relative;padding-left:14px}

/* nav */
.main-nav{left:105px;top:137px;width:701px;height:46px;background:var(--ink);display:flex;justify-content:space-between;padding:0 8px}
.main-nav a{flex:none;white-space:nowrap;color:#ddd;text-decoration:none;font-size:7.5px;font-weight:600;text-transform:uppercase;display:flex;align-items:center;padding:0 12px;border-right:1px solid #3d3d3d}
.main-nav a:last-child{border-right:none}
.main-nav a.active{background:var(--gold);color:var(--white)}

/* hero */
.hero{left:105px;top:194px;width:701px;height:228px;overflow:hidden}
.hero-photo{position:absolute;inset:0;background:linear-gradient(90deg,#5b5148,#8b7c6a 40%,#a99a86 70%)}
.consult{position:absolute;left:0;top:0;width:154px;height:228px;background:rgba(30,28,26,.62);padding:8px 12px}
.consult small{display:block;font-size:6.5px;color:#eee;white-space:nowrap}
.consult h3{font-size:10px;color:var(--white);font-weight:700;margin-top:2px;white-space:nowrap}
.consult .tag{font-size:6.5px;font-style:italic;font-weight:700;color:#eee;margin:20px 0 8px 20px}
.field{border:1px solid #ddd;border-radius:2px;height:19px;font-size:6.5px;font-style:italic;color:#eee;padding:5px 9px;margin-bottom:5px}
.field.light{background:rgba(255,255,255,.8);color:#888}
.field.tall{height:46px}
.btn-submit{display:inline-block;background:var(--gold);color:var(--white);font-size:7px;font-weight:700;padding:6px 11px;border-radius:2px;margin-top:1px}
.hero-panel{position:absolute;right:0;top:0;width:250px;height:228px}
.hero-copy{position:absolute;left:513px;top:40px;width:172px;color:var(--white)}
.hero-copy h2{font-family:"Ubuntu",sans-serif;font-weight:500;font-size:15px;line-height:1.4}
.hero-copy p{font-size:7.3px;line-height:1.95;margin-top:8px}
.btn-light{display:inline-block;background:var(--white);color:var(--ink);font-size:7px;padding:7px 11px;border-radius:2px;margin-top:12px}
.dots{display:flex;gap:4px}
.dots i{width:6px;height:6px;border-radius:50%;background:rgba(255,255,255,.4)}
.dots i.on{background:var(--white)}
.hero .dots{position:absolute;left:513px;top:210px}

/* main panel */
.panel{left:105px;top:433px;width:701px;height:653px;background:var(--white)}
.heading{display:flex;align-items:center;gap:6px;font-size:10px;font-weight:700;color:var(--ink);text-transform:uppercase;white-space:nowrap}
.heading::before{content:"";width:3px;height:10px;background:var(--gold)}
.heading::after{content:"";flex:1;height:6px;background:#f4f4f4}
.video{left:123px;top:493px;width:438px;height:227px;border:1px solid var(--line);padding:6px}
.video-frame{width:100%;height:100%;position:relative;background:linear-gradient(180deg,#a9b2a6,#7f8d6c)}
.play{position:absolute;left:50%;top:43%;width:28px;height:28px;margin:-14px;background:rgba(255,255,255,.35);display:flex;align-items:center;justify-content:center}
.controls{position:absolute;left:0;right:0;bottom:0;height:22px;background:#262626;display:flex;align-items:center;gap:8px;padding:0 8px;font-size:6px;color:#999}
.track{flex:1;height:3px;background:#555;position:relative}
.track span{position:absolute;left:0;top:0;width:29%;height:3px;background:var(--gold)}
.track span::after{content:"";position:absolute;right:-3px;top:-2px;width:7px;height:7px;border-radius:50%;background:#fff}

.hours{left:579px;top:468px;width:210px;height:194px;border:1px solid var(--line)}
.hours h4{background:var(--gold);color:var(--white);text-align:center;font-size:10px;height:34px;line-height:34px}
.hours table{width:100%;border-collapse:collapse;font-size:7px}
.hours td{height:22.8px;padding:0 10px;border-bottom:1px solid #eee;white-space:nowrap}
.hours tr:nth-child(odd){background:var(--row)}
.hours td:first-child{color:var(--ink);font-weight:600}
.hours td:last-child{text-align:right;color:#888}
.hours tr.closed td{color:var(--gold)}

.cta{height:46px;display:flex;background:var(--ink);border:1px solid var(--gold)}
.cta .mark{width:46px;background:var(--gold);color:var(--white);display:flex;align-items:center;justify-content:center;font-size:15px;font-weight:700}
.cta .label{padding:8px 0 0 38px;color:var(--white);white-space:nowrap}
.cta small{display:block;font-size:6.5px;font-weight:600}
.cta strong{display:block;font-family:"Ubuntu",sans-serif;font-size:19px;color:var(--gold);line-height:1.1}

.testimonial{left:579px;top:715px;width:210px;height:104px;background:#f1f1f1}
.testimonial blockquote{padding:12px 20px 0 20px;font-size:7px;font-style:italic;line-height:2.1;color:#888;position:relative}
.testimonial blockquote::before{content:"\201C";position:absolute;left:16px;top:2px;font-size:42px;color:#ddd;font-style:normal;line-height:1}
.testimonial blockquote p{text-indent:32px;position:relative}
.testimonial footer{position:absolute;left:0;right:0;bottom:0;height:22px;background:var(--gold);color:var(--white);font-size:6.5px;font-weight:700;display:flex;align-items:center;justify-content:space-between;padding:0 16px}

.welcome-text{left:123px;top:912px;width:325px;font-size:7.3px;line-height:2.02;text-align:justify}
.welcome-photo{left:465px;top:912px;width:324px;height:140px;background:linear-gradient(120deg,#9db36f,#c9b79a 50%,#8aa458)}

/* footer */
.foot-links{left:0;top:1086px;width:912px;height:57px;background:var(--gold)}
.foot-links nav{position:absolute;left:122px;top:24px;font-size:7.5px;color:var(--white);font-weight:600;white-space:nowrap}
.foot-links nav span{margin:0 4px}
.foot-brand{position:absolute;left:716px;top:17px;font-family:"Ubuntu",sans-serif;font-weight:700;color:var(--white);line-height:1}
.foot-brand b{display:block;font-size:13px}
.foot-brand em{display:block;font-style:normal;font-size:7px;letter-spacing:.5px;margin-top:2px}
.foot-bar{left:0;top:1143px;width:912px;height:57px;background:var(--ink);color:var(--white);font-size:7.3px}
.foot-bar .addr{position:absolute;left:122px;top:19px;font-weight:700;line-height:1.5}
.foot-bar .addr i{display:block;font-weight:400;padding-left:27px}
.foot-bar .icons{position:absolute;left:416px;top:16px;display:flex;gap:8px}
.sq{width:22px;height:22px;border:1px solid var(--gold);border-radius:2px;color:var(--gold);font-size:8px;font-weight:700;display:flex;align-items:center;justify-content:center}
.sq.on{background:var(--gold);color:var(--white)}
.foot-bar .copy{position:absolute;right:122px;top:19px;text-align:right;font-weight:700;line-height:1.5}
.foot-bar .copy i{display:block;font-weight:400}
.foot-bar .copy i span{color:var(--gold)}
</style>
</head>
<body>

<header>
  <div class="abs brand"><span class="name">FAIR RIDGE</span><span class="sub">CHIROPRACTIC</span></div>
  <div class="abs social-top" aria-label="Social links">
    <span class="social-dot" aria-label="Chatterly">C</span>
    <span class="social-dot on" aria-label="Plexo+">P+</span>
    <span class="social-dot" aria-label="Vidzio">V</span>
  </div>
  <div class="abs contact-bar">
    <div class="info">
      <div class="item">
        <svg width="16" height="16" viewBox="0 0 24 24"><path fill="#b89a5a" d="M6.6 10.8a15.1 15.1 0 0 0 6.6 6.6l2.2-2.2c.3-.3.7-.4 1-.2 1.1.4 2.3.6 3.6.6.6 0 1 .4 1 1V20c0 .6-.4 1-1 1A17 17 0 0 1 3 4c0-.6.4-1 1-1h3.5c.6 0 1 .4 1 1 0 1.3.2 2.5.6 3.6.1.3 0 .7-.2 1z"/></svg>
        <div><b>555-014-2297</b><i>info@example.com</i></div>
      </div>
      <div class="item">
        <svg width="18" height="16" viewBox="0 0 24 22"><path fill="#b89a5a" d="M12 1 1 11h3v10h6v-6h4v6h6V11h3z"/></svg>
        <div><b>4172 North Maple Blvd, Suite #7</b><i>Brookhaven, FL 34720</i></div>
      </div>
    </div>
    <div class="appt">
      <svg width="132" height="35" viewBox="0 0 132 35"><path d="M0 0h12l-4 17.5L12 35H0l-6-17.5z" fill="#2c2c2c"/><path d="M12 0h120v35H12L6 17.5z" fill="#b89a5a"/><path d="M8 17.5 12 0h4l-4 17.5L16 35h-4z" fill="#a48748"/></svg>
      <span>MAKE AN APPOINTMENT</span>
    </div>
  </div>
</header>

<nav class="abs main-nav">
  <a href="#">Home</a>
  <a href="#" class="active">Why Fair Ridge?</a>
  <a href="#">How Chiropractic Helps</a>
  <a href="#">Ask the Doctor</a>
  <a href="#">Work Place Wellness</a>
  <a href="#">Request an Appointment</a>
  <a href="#">Blog</a>
  <a href="#">Contact Us</a>
</nav>

<section class="abs hero">
  <div class="hero-photo" role="img" aria-label="Photo of the doctor and a smiling assistant in the clinic"></div>
  <form class="consult">
    <small>CONTACT US NOW &amp; GET YOUR</small>
    <h3>FREE CONSULTATION</h3>
    <p class="tag">WELLNESS BEGINS HERE</p>
    <div class="field">First Name</div>
    <div class="field light">Last Name</div>
    <div class="field">Phone Number</div>
    <div class="field tall">Comments ...</div>
    <span class="btn-submit">Submit ➜</span>
  </form>
  <svg class="hero-panel" viewBox="0 0 250 228" preserveAspectRatio="none">
    <path d="M6 0h244v228H12C-6 200 36 160 30 110 26 60-8 40 6 0z" fill="#b89a5a"/>
    <path d="M6 0C-8 40 26 60 30 110 36 160-6 200 12 228" stroke="#fff" stroke-width="3" fill="none"/>
  </svg>
  <div class="hero-copy">
    <h2>Interested in<br>Becoming a Patient?</h2>
    <p>Proin sit amet venenatis ante. Nulla lorem felis, maximus tincidunt felis nec, mattis con dimentum enim. Maecenas non sodales nund.</p>
    <span class="btn-light">Read More</span>
  </div>
  <div class="dots"><i></i><i class="on"></i><i></i><i></i></div>
</section>

<main>
  <div class="abs panel"></div>

  <h3 class="abs heading" style="left:123px;top:465px;width:438px">Our Videos</h3>
  <div class="abs video">
    <div class="video-frame" role="img" aria-label="Video still of a smiling family outdoors">
      <div class="play"><svg width="10" height="10" viewBox="0 0 10 10"><path d="M2 1l7 4-7 4z" fill="#fff"/></svg></div>
      <div class="controls">
        <svg width="8" height="8" viewBox="0 0 10 10"><path d="M2 1l7 4-7 4z" fill="#999"/></svg>
        <span>00:28</span><div class="track"><span></span></div><span>02:36</span>
        <svg width="9" height="8" viewBox="0 0 10 10"><path d="M1 3h2l3-2v8L3 7H1z" fill="#999"/></svg>
        <svg width="8" height="8" viewBox="0 0 10 10"><path d="M1 9 9 1M6 1h3v3M1 6v3h3" stroke="#999" fill="none"/></svg>
      </div>
    </div>
  </div>

  <h3 class="abs heading" style="left:123px;top:746px;width:438px">We're on Social Medias</h3>
  <a class="abs cta" style="left:123px;top:773px;width:210px" aria-label="Rate us on Plexo">
    <span class="mark">P</span><span class="label"><small>RATE US ON</small><strong>PLEXO</strong></span>
  </a>
  <a class="abs cta" style="left:351px;top:773px;width:210px" aria-label="Find us on Chatterly">
    <span class="mark">C</span><span class="label"><small>FIND US ON</small><strong>CHATTERLY</strong></span>
  </a>

  <aside class="abs hours">
    <h4>OFFICE HOURS</h4>
    <table>
      <tr><td>Monday</td><td>8:00-11:00 AM, 2:00-5:00 PM</td></tr>
      <tr><td>Tuesday</td><td>8:30-11:00 AM, 2:00-5:30 PM</td></tr>
      <tr><td>Wednesday</td><td>8:00-11:00 AM, 2:00-5:00 PM</td></tr>
      <tr><td>Thursday</td><td>10:00-12:00 AM, 2:30-5:00 PM</td></tr>
      <tr><td>Friday</td><td>8:00-10:00 AM, 1:00-5:00 PM</td></tr>
      <tr class="closed"><td>Saturday</td><td>Closed</td></tr>
      <tr class="closed"><td>Sunday</td><td>Closed</td></tr>
    </table>
  </aside>

  <h3 class="abs heading" style="left:579px;top:688px;width:210px">Patient Testimonials</h3>
  <div class="abs testimonial">
    <blockquote><p>Pellentesque habitant morbi tristique senectus et netus et malesuada fames ac turpis egestas. Donec faucibus aliquet dui, nec congue orci sagittis eget.</p></blockquote>
    <footer><span>- Mr. Daniel Harrow -</span><span class="dots"><i></i><i class="on"></i><i></i><i></i></span></footer>
  </div>

  <div class="abs" style="left:105px;top:853px;width:701px;height:1px;background:#f0f0f0"></div>

  <h3 class="abs heading" style="left:123px;top:886px;width:666px">Welcome Letter</h3>
  <div class="abs welcome-text">
    <p>Hello Dear Visitor,</p>
    <p>Vestibulum malesuada tortor volutpat risus finibus, in consequat nibh dictum. Pellentesque vestibulum nisi nisl, vel accumsan dui consequat sed. Integer non justo et mi interdum pretium. Proin ut pulvinar eros. Pellentesque at luctus odio, a ullamcorper urna. Nam semper feugiat massa non pulvinar. Curabitur sagittis, odio eget posuere ultricies, sem nisi pulvinar turpis, at laoreet arcu neque lacinia odio. Nulla nec nunc ac felis auctor fermentum quis ut justo. Donec ultricies feugiat accumsan. Integer leo justo, dapibus id mauris quis, vestibulum rutrum arcu. Etiam sed ipsum eu augue condimentum ullamcorper vel ac sapien. Cras sed lorem et est interdum commodo vitae sit amet orci. Ut mattis tempor metus sed venenatis.</p>
  </div>
  <div class="abs welcome-photo" role="img" aria-label="Photo of a happy family of four outdoors"></div>
</main>

<footer>
  <div class="abs foot-links">
    <nav>Home<span>|</span>Why Fair Ridge?<span>|</span>How Chiropractic Helps<span>|</span>Ask the Doctor<span>|</span>Work Place Wellness<span>|</span>Request an Appointment<span>|</span>Blog<span>|</span>Contact Us</nav>
    <div class="foot-brand"><b>FAIR RIDGE</b><em>CHIROPRACTIC</em></div>
  </div>
  <div class="abs foot-bar">
    <div class="addr">4172 North Maple Blvd, Suite #7<i>Brookhaven, FL 34720</i></div>
    <div class="icons">
      <span class="sq" aria-label="Chatterly">C</span>
      <span class="sq on" aria-label="Plexo+">P+</span>
      <span class="sq" aria-label="Vidzio">V</span>
    </div>
    <div class="copy">Copyright © 2015, Fair Ridge Chiropractic<i>Powered by <span>Crestline Pixel Group</span></i></div>
  </div>
</footer>

</body>
</html>
```